Help me make landing pages for my web application that are mobile friendly

I need to make 2 mobile friendly landing pages for an application. The 2 pages will be related. First I need a home page and then I need a working page. I do not want to change the color scheme or logos. Just layout and design.

```html
<!DOCTYPE html>
<html lang="en">
<head>
<meta charset="utf-8">
<title>ShiftCover – Mobile Screens</title>
<link href="https://fonts.googleapis.com/css2?family=Poppins:wght@400;500;600;700&display=swap" rel="stylesheet">
<style>
:root{
  --bg:#e4e4e4;
  --cyan:#27b2d6;
  --purple:#6656a6;
  --ink:#222;
  --muted:#666;
  --field:#efefef;
  --line:#e3e3e3;
  --green:#6cc070;
  --red:#d8262c;
  --orange:#f5a04a;
  --close:#e0435a;
}
*{box-sizing:border-box;margin:0;padding:0}
html,body{width:693px;height:1200px;overflow:hidden}
body{background:var(--bg);font-family:'Poppins',sans-serif;color:var(--ink);position:relative}
.brand-header{position:absolute;top:52px;left:0;width:693px;text-align:center;font-size:44px;font-weight:600;color:var(--purple);letter-spacing:-0.5px}
.screen{position:absolute;width:194px;border-radius:22px;overflow:hidden;background:#fff;box-shadow:0 10px 30px rgba(80,90,130,.25)}
.splash{left:128px;top:166px;height:421px;background:linear-gradient(160deg,#cdeef5 0%,#fff 40%,#fff 60%,#e3e1fb 100%)}
.assignments{left:128px;top:643px;height:455px;background:linear-gradient(170deg,#e3f5fa 0%,#fff 25%,#fff 100%)}
.opening{left:376px;top:405px;height:455px;background:linear-gradient(170deg,#dff3f9 0%,#fff 30%,#eeecfb 85%,#fff 100%)}
.status-time{position:absolute;top:6px;left:22px;font-size:7px;font-weight:600}
.splash-name{position:absolute;top:94px;width:100%;text-align:center;font-size:21px;font-weight:600;color:var(--purple)}
.home-bar{position:absolute;bottom:20px;left:63px;width:68px;height:3px;border-radius:2px;background:var(--purple)}
.topbar{position:absolute;top:25px;left:10px;right:10px;display:flex;justify-content:space-between;align-items:center;font-size:5.5px;font-weight:600}
.topbar svg{width:8px;height:8px}
.tabs{position:absolute;top:42px;left:10px;right:10px;display:flex;gap:3px}
.tab{flex:1;height:16px;border-radius:8px;font-size:4.8px;font-weight:600;display:flex;align-items:center;justify-content:center;background:#e7eaec;color:#333}
.tab.active{background:var(--cyan);color:#fff}
.section-title{position:absolute;top:69px;left:10px;font-size:7px;font-weight:600}
.list{position:absolute;top:82px;left:10px;right:10px;display:flex;flex-direction:column;gap:6px}
.card{background:#fff;border:1px solid var(--line);border-radius:10px;position:relative;height:70px}
.card .label{position:absolute;top:8px;left:11px;font-size:4.5px;font-weight:600}
.edit{position:absolute;top:5px;right:9px;width:11px;height:11px;border-radius:50%;background:#f0f0f0;display:flex;align-items:center;justify-content:center}
.edit svg{width:6px;height:6px}
.photo{position:absolute;top:19px;left:11px;width:38px;height:38px;border-radius:7px;background:linear-gradient(150deg,#b8bcc4,#6f6a66)}
.photo::after{content:"";position:absolute;top:-1px;right:-2px;width:5px;height:5px;border-radius:50%;background:var(--green);border:1px solid #fff}
.name{position:absolute;top:20px;left:56px;font-size:6.3px;font-weight:600;color:var(--cyan)}
.role{position:absolute;top:29px;left:56px;font-size:4.3px;color:var(--muted)}
.rule{position:absolute;top:38px;left:56px;right:9px;height:1px;background:var(--line)}
.meta{position:absolute;top:42px;left:56px;right:9px;display:grid;grid-template-columns:30px 35px 1fr;font-size:4.3px}
.meta b{font-weight:600;display:block;margin-bottom:2px}
.meta span{font-size:3.6px;color:var(--muted)}
.pill{display:inline-block;padding:1px 4px;border-radius:5px;font-size:3.4px;font-weight:600;color:#fff}
.pill.active{background:var(--green)}.pill.canceled{background:var(--red)}.pill.complete{background:var(--orange)}
.nav{position:absolute;bottom:0;left:0;right:0;height:30px;background:#fff;border-top:1px solid var(--line);display:flex;justify-content:space-around;align-items:center;padding:0 8px}
.nav-item{display:flex;flex-direction:column;align-items:center;gap:2px;font-size:3.8px;font-weight:500;color:#777}
.nav-item svg{width:9px;height:9px}
.nav-item.current{color:var(--purple)}
.panel{position:absolute;left:10px;right:10px;background:#fff;border:1px solid var(--line);border-radius:11px}
.panel h3{position:absolute;left:16px;font-size:6.8px;font-weight:600}
.toggle{position:absolute;right:12px;width:9px;height:9px;border-radius:50%;background:#222;display:flex;align-items:center;justify-content:center}
.toggle svg{width:5px;height:5px}
.info{position:absolute;top:30px;left:16px;display:grid;grid-template-columns:63px 1fr;row-gap:1.6px;font-size:4.3px}
.info dt{font-weight:500}.info dd{color:var(--muted)}
.field{position:absolute;left:16px;right:16px;background:var(--field);border-radius:8px;font-size:5px;color:var(--muted);padding:6px 8px}
.btn{position:absolute;height:16px;border-radius:8px;color:#fff;font-size:4.8px;font-weight:600;display:flex;align-items:center;justify-content:center;gap:3px}
.btn svg{width:5px;height:5px}
.small-label{position:absolute;left:16px;font-size:4.3px;font-weight:600}
</style>
</head>
<body>

<div class="brand-header">ShiftCover</div>

<!-- Home / splash screen -->
<section class="screen splash">
  <div class="status-time">9:41</div>
  <div class="splash-name">ShiftCover</div>
  <div class="home-bar"></div>
</section>

<!-- Assignments screen -->
<section class="screen assignments">
  <div class="status-time">9:41</div>
  <div class="topbar">
    <span>‹ &nbsp;MESSAGE</span>
    <svg viewBox="0 0 10 10"><path d="M5 1a3 3 0 0 1 3 3v3l1 1H1l1-1V4a3 3 0 0 1 3-3z" fill="#222"/><circle cx="5" cy="9" r="1" fill="#222"/></svg>
  </div>
  <div class="tabs"><div class="tab active">My Assignments</div><div class="tab">Available Openings</div></div>
  <div class="section-title">My Assignments</div>
  <div class="list">
    <article class="card">
      <div class="label">Subbing For:</div>
      <div class="edit"><svg viewBox="0 0 10 10"><path d="M2 8l1-3 4-4 2 2-4 4z" fill="none" stroke="#333"/></svg></div>
      <div class="photo" role="img" aria-label="Portrait photo of the staff member"></div>
      <div class="name">Dorian Hale</div><div class="role">Administrator</div><div class="rule"></div>
      <div class="meta"><div><b>Location:</b><span>CRHS</span></div><div><b>Status:</b><span class="pill active">Active</span></div><div><b>Time Slots:</b><span>07/26 - 08/07 (14h 15m)</span></div></div>
    </article>
    <article class="card">
      <div class="label">Subbing For:</div>
      <div class="edit"><svg viewBox="0 0 10 10"><path d="M2 8l1-3 4-4 2 2-4 4z" fill="none" stroke="#333"/></svg></div>
      <div class="photo" role="img" aria-label="Portrait photo of the staff member"></div>
      <div class="name">Priya Castell</div><div class="role">Teacher</div><div class="rule"></div>
      <div class="meta"><div><b>Location:</b><span>CRHS</span></div><div><b>Status:</b><span class="pill canceled">Canceled</span></div><div><b>Time Slots:</b><span>07/31 - 07/31 (9h 0m)</span></div></div>
    </article>
    <article class="card">
      <div class="label">Subbing For:</div>
      <div class="edit"><svg viewBox="0 0 10 10"><path d="M2 8l1-3 4-4 2 2-4 4z" fill="none" stroke="#333"/></svg></div>
      <div class="photo" role="img" aria-label="Portrait photo of the staff member"></div>
      <div class="name">Owen Raske</div><div class="role">Teacher</div><div class="rule"></div>
      <div class="meta"><div><b>Location:</b><span>CRHS</span></div><div><b>Status:</b><span class="pill complete">Complete</span></div><div><b>Time Slots:</b><span>07/31 - 07/31 (9h 0m)</span></div></div>
    </article>
    <article class="card">
      <div class="label">Subbing For:</div>
      <div class="edit"><svg viewBox="0 0 10 10"><path d="M2 8l1-3 4-4 2 2-4 4z" fill="none" stroke="#333"/></svg></div>
      <div class="photo" role="img" aria-label="Portrait photo of the staff member"></div>
      <div class="name">Lena Farrow</div><div class="role">Teacher</div><div class="rule"></div>
      <div class="meta"><div><b>Location:</b><span>CRHS</span></div><div><b>Status:</b><span class="pill active">Active</span></div><div><b>Time Slots:</b><span>07/26 - 08/07 (14h 15m)</span></div></div>
    </article>
    <article class="card">
      <div class="label">Subbing For:</div>
      <div class="edit"><svg viewBox="0 0 10 10"><path d="M2 8l1-3 4-4 2 2-4 4z" fill="none" stroke="#333"/></svg></div>
      <div class="photo" role="img" aria-label="Portrait photo of the staff member"></div>
      <div class="name">Priya Castell</div><div class="role">Teacher</div>
    </article>
  </div>
  <nav class="nav">
    <div class="nav-item"><svg viewBox="0 0 10 10"><path d="M1 5l4-4 4 4v4H6V6H4v3H1z" fill="#333"/></svg>HOME</div>
    <div class="nav-item"><svg viewBox="0 0 10 10"><path d="M2 1h4l2 2v6H2z" fill="#333"/></svg>OPENINGS</div>
    <div class="nav-item current"><svg viewBox="0 0 10 10"><path d="M2 1h4l2 2v6H2z" fill="#6656a6"/></svg>ASSIGNMENTS</div>
    <div class="nav-item"><svg viewBox="0 0 10 10"><circle cx="5" cy="5" r="4" fill="none" stroke="#333"/><circle cx="5" cy="4" r="1.5" fill="#333"/></svg>SUPPORT</div>
    <div class="nav-item"><svg viewBox="0 0 10 10"><path d="M1 1h5v8H1z" fill="#333"/><path d="M6 5h3M8 3l1 2-1 2" stroke="#333" fill="none"/></svg>LOG OUT</div>
  </nav>
</section>

<!-- Opening detail screen -->
<section class="screen opening">
  <div class="status-time">9:41</div>
  <div class="topbar">
    <span>‹ &nbsp;MESSAGE</span>
    <svg viewBox="0 0 10 10"><path d="M5 1a3 3 0 0 1 3 3v3l1 1H1l1-1V4a3 3 0 0 1 3-3z" fill="#222"/><circle cx="5" cy="9" r="1" fill="#222"/></svg>
  </div>

  <div class="panel" style="top:42px;height:220px">
    <h3 style="top:12px">Opening Information</h3>
    <div class="toggle" style="top:13px"><svg viewBox="0 0 10 10"><path d="M2 4l3 3 3-3" stroke="#fff" fill="none" stroke-width="1.5"/></svg></div>
    <dl class="info">
      <dt>Summary:</dt><dd>Testing-test</dd>
      <dt>Location:</dt><dd>Cedar Ridge Elementary School</dd>
      <dt>Type:</dt><dd>Vacancy</dd>
      <dt>Regular Staff:</dt><dd>Owen Raske</dd>
      <dt>Assignment Category:</dt><dd>Teacher Department</dd>
    </dl>
    <h3 style="top:75px">Description</h3>
    <div class="field" style="top:89px;height:31px">Some line goes here</div>
    <h3 style="top:123px">Comments</h3>
    <div class="field" style="top:134px;height:31px">Write a comment or upload a file...</div>
    <div class="field" style="top:171px;height:16px;padding:4px 8px;font-size:4.3px;color:#222">⚲ No comment or files uploaded</div>
    <div class="btn" style="top:194px;left:16px;width:69px;background:var(--cyan)"><svg viewBox="0 0 10 10"><path d="M1 5l8-4-3 8-1-3z" fill="#fff"/></svg>POST</div>
    <div class="btn" style="top:194px;right:16px;width:69px;background:var(--purple)"><svg viewBox="0 0 10 10"><path d="M5 1v6M2 4l3-3 3 3M1 9h8" stroke="#fff" fill="none"/></svg>UPLOAD</div>
  </div>

  <div class="panel" style="top:272px;height:63px">
    <h3 style="top:10px">Additional Details</h3>
    <div class="toggle" style="top:11px"><svg viewBox="0 0 10 10"><path d="M2 4l3 3 3-3" stroke="#fff" fill="none" stroke-width="1.5"/></svg></div>
    <div class="small-label" style="top:26px">Parking Spot</div>
    <div class="field" style="top:36px;height:15px"></div>
  </div>

  <div class="panel" style="top:345px;height:30px">
    <h3 style="top:9px">Time Slot</h3>
    <div class="toggle" style="top:10px"><svg viewBox="0 0 10 10"><path d="M4 2l3 3-3 3" stroke="#fff" fill="none" stroke-width="1.5"/></svg></div>
  </div>

  <div class="btn" style="top:383px;left:10px;width:85px;height:20px;background:var(--purple);border-radius:10px">✔ SAVE</div>
  <div class="btn" style="top:383px;right:10px;width:85px;height:20px;border:1px solid var(--close);color:var(--close);background:#fff;border-radius:10px">✖ CLOSE</div>

  <nav class="nav">
    <div class="nav-item"><svg viewBox="0 0 10 10"><path d="M1 5l4-4 4 4v4H6V6H4v3H1z" fill="#333"/></svg>HOME</div>
    <div class="nav-item"><svg viewBox="0 0 10 10"><path d="M2 1h4l2 2v6H2z" fill="#333"/></svg>OPENINGS</div>
    <div class="nav-item"><svg viewBox="0 0 10 10"><path d="M2 1h4l2 2v6H2z" fill="#333"/></svg>ASSIGNMENTS</div>
    <div class="nav-item"><svg viewBox="0 0 10 10"><circle cx="5" cy="5" r="4" fill="none" stroke="#333"/><circle cx="5" cy="4" r="1.5" fill="#333"/></svg>SUPPORT</div>
    <div class="nav-item"><svg viewBox="0 0 10 10"><path d="M1 1h5v8H1z" fill="#333"/><path d="M6 5h3M8 3l1 2-1 2" stroke="#333" fill="none"/></svg>LOG OUT</div>
  </nav>
</section>

</body>
</html>
```